Academic and Business book cover

I need a book cover for my academic and business book.
The focus is in international / global negotiation and influence (how to negotiate across cultures).
The book will be published on Zelvorn, both in Vaspet and printed edition. therefore I need something that works under Zelvorn guidelines.The final design should be elegant and still be able to stand out against the competition.
I would like to have orange+grey for the text colors on the cover, even if different options are welcome.
Title and my name are in the attached word doc.

Target Market(s)

graduates, Phds, from international business schools. Managers

Industry/Entity Type

Business

Font styles to use
Serif
Sans Serif

Colors

Designer to choose colors to be used in the design.

Requirements
Must have
• The title and my name should have elegant fonts.
Nice to have
• pictures of the world that don't have the "usual" Europe in the centre.

```html
<!DOCTYPE html>
<html lang="en">
<head>
<meta charset="utf-8">
<title>The 3Cs Method – Cover Options</title>
<link rel="stylesheet" href="https://fonts.googleapis.com/css2?family=Work+Sans:wght@500;600;700&display=swap">
<style>
  :root {
    --page-bg: #ffffff;
    --cover-bg: #2b2b2b;
    --slate: #3e4a4f;
    --plum: #6d3f5e;
    --ochre: #a87332;
    --blue-band: #315a87;
    --teal: #4a8a90;
    --title-orange: #f7a93b;
    --subtitle-white: #ecebe8;
  }
  * { margin: 0; padding: 0; box-sizing: border-box; }
  html, body {
    width: 1200px; height: 1000px; overflow: hidden;
    background: var(--page-bg);
    font-family: "Work Sans", Arial, sans-serif;
  }
  .cover {
    position: absolute; top: 205px;
    width: 432px; height: 640px;
    background: var(--cover-bg);
    overflow: hidden;
    box-shadow: 6px 6px 14px rgba(0,0,0,0.25);
  }
  .cover--sentence { left: 93px; }
  .cover--caps { left: 664px; }
  .cover-art { position: absolute; inset: 0; width: 432px; height: 640px; }
  .cover-title, .cover-subtitle, .cover-author {
    position: absolute; left: 0; width: 100%; text-align: center; white-space: nowrap;
  }
  .cover-title {
    top: 66px; font-size: 28px; font-weight: 700; color: var(--title-orange);
  }
  .cover-subtitle {
    top: 117px; font-size: 20.5px; font-weight: 600; line-height: 34px;
    color: var(--subtitle-white);
  }
  .cover-author {
    top: 589px; font-size: 21px; font-weight: 700; color: var(--title-orange);
  }
  .cover--caps .cover-title { font-size: 25.5px; letter-spacing: 0.6px; top: 69px; }
  .cover--caps .cover-subtitle {
    font-size: 16px; letter-spacing: 1.2px; line-height: 33px; top: 117px;
  }
</style>
</head>
<body>
<svg width="0" height="0" style="position:absolute">
  <defs>
    <radialGradient id="globe-fill" cx="42%" cy="40%" r="65%">
      <stop offset="0%" stop-color="#d99a5c"/>
      <stop offset="55%" stop-color="#b86a58"/>
      <stop offset="100%" stop-color="#7a8a5a"/>
    </radialGradient>
    <symbol id="cover-art" viewBox="0 0 432 640">
      <rect x="60" y="50" width="312" height="2" fill="var(--slate)"/>
      <rect x="60" y="176" width="312" height="2" fill="var(--slate)"/>
      <rect x="0" y="214" width="432" height="22" fill="var(--plum)"/>
      <rect x="0" y="250" width="432" height="44" fill="var(--ochre)"/>
      <rect x="0" y="308" width="432" height="96" fill="var(--blue-band)"/>
      <rect x="0" y="418" width="432" height="44" fill="var(--teal)"/>
      <rect x="0" y="476" width="432" height="22" fill="var(--plum)"/>
      <rect x="0" y="512" width="432" height="10" fill="var(--slate)"/>
      <circle cx="216" cy="358" r="140" fill="var(--cover-bg)"/>
      <circle cx="216" cy="358" r="128" fill="url(#globe-fill)"/>
      <rect x="60" y="562" width="312" height="2" fill="var(--slate)"/>
    </symbol>
  </defs>
</svg>

<section class="cover cover--sentence">
  <svg class="cover-art" viewBox="0 0 432 640" role="img" aria-label="Globe centred on the Americas set over horizontal colour bands">
    <use href="#cover-art"/>
  </svg>
  <h1 class="cover-title">The 3Cs Method</h1>
  <p class="cover-subtitle">Practical Bargaining and Persuasion<br>Methods for Worldwide Leadership</p>
  <p class="cover-author">Darvesh K. Molan</p>
</section>

<section class="cover cover--caps">
  <svg class="cover-art" viewBox="0 0 432 640" role="img" aria-label="Globe centred on the Americas set over horizontal colour bands">
    <use href="#cover-art"/>
  </svg>
  <h1 class="cover-title">THE 3CS METHOD</h1>
  <p class="cover-subtitle">PRACTICAL BARGAINING AND PERSUASION<br>METHODS FOR WORLDWIDE LEADERSHIP</p>
  <p class="cover-author">Darvesh K. Molan</p>
</section>
</body>
</html>
```